Business card design for a dynamic IT consulting company

We need a business card design for a young firm, specialized in the Telecommunications/Consulting industry. The name of the company is Quindor and Partners Business Consulting Ltd. (Short name: Quindor and Partnes)
Quindor = solve read reverse, so we aim to be uncomplicated and solution-oriented. The small pipe in our logo is also related to the word solve. So we need a new business card design, which is simple, eye catching and something non traditional (I would probably prefer a square shaped design rather than a rectangle, but open for suggestions). Attached our logo.

Target Market(s)

Usually our customers are Tier1 Telecoms providers (Q-Netra, Palorix, etc) and their executives.

Industry/Entity Type

Business

Contact Information for Business Card

Name: Bence Tolnavari
Email: b.tolnavari@quindor.hu
Web: www.quindor.hu
Mobile: +36 30 518 2769
Title: Managing Director

Optional:
Company name: Quindor and Partners Ltd.
Address: 1087 Budapest, Tolvenka str. 28/C, Hungary

Font styles to use
Other font styles liked:
• helveticaneue_medium, Prime Regular are used now.

Colors

Designer to choose colors to be used in the design.

Requirements
Must have
• I would like to have a 2 sided design.
Nice to have
• I thought if we make the logo a bit bigger (without the company name), that could go to the back with the company name below. I though, if the pipe in the logo is somehow touchable on the business card, would be nice and unique.

```html
<!DOCTYPE html>
<html lang="en">
<head>
<meta charset="utf-8">
<title>Quindor and Partners – Business Card</title>
<link rel="stylesheet" href="https://fonts.googleapis.com/css2?family=Arimo:wght@400;700&display=swap">
<style>
  :root {
    --backdrop: #e9e7e3;
    --card-white: #f7f7f6;
    --card-dark: #1c1d21;
    --brand-blue: #1a9be0;
    --text-grey: #5d5f63;
    --band-grey: #636568;
    --shadow: rgba(0, 0, 0, 0.28);
  }
  html, body {
    margin: 0;
    padding: 0;
    width: 1200px;
    height: 960px;
    overflow: hidden;
    background: var(--backdrop);
    font-family: "Arimo", "Helvetica Neue", Arial, sans-serif;
  }
  .stage {
    position: relative;
    width: 1200px;
    height: 960px;
  }
  .card {
    position: absolute;
    top: 305px;
    width: 343px;
    height: 343px;
    box-shadow: 2px 3px 6px var(--shadow);
    overflow: hidden;
  }

  /* Front side */
  .card-front {
    left: 200px;
    background: var(--card-white);
    color: var(--text-grey);
    text-align: center;
  }
  .company-mark {
    position: absolute;
    top: 36px;
    left: 0;
    width: 100%;
    display: flex;
    justify-content: center;
    align-items: center;
    gap: 9px;
  }
  .company-mark .mark-square {
    width: 14px;
    height: 14px;
    background: var(--brand-blue);
  }
  .company-mark .mark-name {
    font-size: 25px;
    font-weight: 400;
    color: var(--text-grey);
    letter-spacing: 0.2px;
  }
  .person-name {
    position: absolute;
    top: 125px;
    width: 100%;
    margin: 0;
    font-size: 19px;
    font-weight: 700;
    color: var(--brand-blue);
    letter-spacing: 0.3px;
  }
  .person-title {
    position: absolute;
    top: 149px;
    width: 100%;
    margin: 0;
    font-size: 14.5px;
    letter-spacing: 0.3px;
  }
  .address {
    position: absolute;
    top: 180px;
    width: 100%;
    margin: 0;
    font-style: normal;
    font-size: 13.5px;
    line-height: 18px;
  }
  .contact {
    position: absolute;
    top: 246px;
    width: 100%;
    font-size: 13.5px;
    line-height: 19px;
  }
  .contact-line {
    display: flex;
    justify-content: center;
    align-items: center;
    gap: 4px;
  }
  .contact-line svg { fill: var(--brand-blue); }
  .rule-blue {
    position: absolute;
    left: 0;
    top: 315px;
    width: 100%;
    height: 3px;
    background: var(--brand-blue);
  }
  .band-grey {
    position: absolute;
    left: 0;
    top: 321px;
    width: 100%;
    height: 22px;
    background: var(--band-grey);
  }

  /* Back side */
  .card-back {
    left: 651px;
    background: var(--card-dark);
  }
  .back-pattern {
    position: absolute;
    inset: 0;
    background: radial-gradient(circle at 70% 70%, #24303a 0%, #1f2229 45%, var(--card-dark) 100%);
  }
  .website {
    position: absolute;
    left: 219px;
    top: 297px;
    margin: 0;
    font-size: 13.5px;
    color: #ffffff;
    letter-spacing: 0.2px;
  }
</style>
</head>
<body>
<main class="stage">
  <section class="card card-front" aria-label="Business card front">
    <div class="company-mark">
      <span class="mark-square"></span>
      <span class="mark-name">Quindor &amp; Partners</span>
    </div>
    <h1 class="person-name">BENCE TOLNAVARI</h1>
    <p class="person-title">MANAGING DIRECTOR</p>
    <address class="address">
      Quindor and Partners Ltd.<br>
      1087 Budapest<br>
      Tolvenka str. 28/C, Hungary
    </address>
    <div class="contact">
      <div class="contact-line">
        <svg width="9" height="14" viewBox="0 0 9 14" aria-hidden="true">
          <path d="M1.5 0h6A1.5 1.5 0 0 1 9 1.5v11A1.5 1.5 0 0 1 7.5 14h-6A1.5 1.5 0 0 1 0 12.5v-11A1.5 1.5 0 0 1 1.5 0zM1.5 2v9h6V2z"/>
        </svg>
        <span>+36 30 518 2769</span>
      </div>
      <div class="contact-line">
        <svg width="11" height="8" viewBox="0 0 11 8" aria-hidden="true">
          <path d="M0 0h11v1L5.5 4.5 0 1z M0 2.2l5.5 3.5L11 2.2V8H0z"/>
        </svg>
        <span>b.tolnavari@quindor.hu</span>
      </div>
    </div>
    <div class="rule-blue"></div>
    <div class="band-grey"></div>
  </section>

  <section class="card card-back" aria-label="Business card back">
    <div class="back-pattern" role="img" aria-label="Dark field with a faint grid of small blue, magenta and grey squares gathering toward the lower right"></div>
    <p class="website">www.quindor.hu</p>
  </section>
</main>
</body>
</html>
```